Web design required

1-We need a web design for existing company based in New Zealand
2-We build residential house and light commercial
3-We has in-house designer which allow us can provide interior design
4-We modeling project before site construction, which enable both client and construction team to visually analysis whole project,

Target Market(s)

middle class residential house market
Ref: http://www.parvellbuilders.co.nz/

Industry/Entity Type

Construction Company

Number of Pages Required

1 page

Font styles to use
Sans Serif
Other font styles liked:
• Such as : Central Gothic or similar which has more design taste

Colors

Designer to choose colors to be used in the design.

Requirements
Must have
• Front sheet, contact information, sample project

```html
<!DOCTYPE html>
<html lang="en">
<head>
<meta charset="utf-8">
<title>Kowhai Homes — Residential &amp; Light Commercial Builders</title>
<link href="https://fonts.googleapis.com/css2?family=Lato:wght@400;700;900&family=Open+Sans:wght@400;600;700&display=swap" rel="stylesheet">
<style>
:root{
  --blue:#1a6cb1;
  --blue-dark:#0d4f8b;
  --blue-deep:#0a3f72;
  --ink:#333b44;
  --muted:#6b737c;
  --line:#dde3ea;
  --white:#ffffff;
}
*{margin:0;padding:0;box-sizing:border-box}
html,body{width:1200px;height:4286px;overflow:hidden}
body{position:relative;background:var(--white);font-family:"Open Sans",Arial,sans-serif;color:var(--ink)}
.abs{position:absolute}
.heading{font-family:"Lato",Arial,sans-serif;font-weight:900;color:var(--blue);text-transform:uppercase;letter-spacing:.5px}
.eyebrow{font-family:"Lato",Arial,sans-serif;font-size:20px;color:var(--muted);text-transform:uppercase;letter-spacing:.5px}
.read-more{font-family:"Lato",Arial,sans-serif;font-size:14px;font-weight:900;color:var(--blue);text-decoration:underline;text-transform:uppercase}
.btn{display:inline-block;background:var(--blue);color:var(--white);font-family:"Lato",Arial,sans-serif;font-size:20px;text-transform:uppercase;border-radius:6px;text-align:center;box-shadow:0 4px 8px rgba(0,0,0,.25)}
.photo{position:absolute}

/* hero */
.hero{position:absolute;left:0;top:0;width:1200px;height:677px;overflow:hidden}
.hero-overlay{position:absolute;inset:0}
.brand{position:absolute;left:77px;top:22px;display:flex;align-items:center;gap:14px}
.brand-square{width:64px;height:64px;background:var(--blue-dark);border-radius:6px}
.brand-name{font-family:"Lato",Arial,sans-serif;font-weight:700;font-size:30px;line-height:32px;color:var(--blue-dark);letter-spacing:3px;text-transform:uppercase}
.nav{position:absolute;left:528px;top:60px;display:flex;gap:32px;font-family:"Lato",Arial,sans-serif;font-size:17px;color:var(--white);text-transform:uppercase}
.nav-active{border-bottom:2px solid var(--white);padding-bottom:6px}
.phone-box{position:absolute;left:948px;top:14px;width:176px;height:40px;border:2px solid var(--white);border-radius:6px;color:var(--white);font-family:"Lato",Arial,sans-serif;font-weight:700;font-size:20px;display:flex;align-items:center;justify-content:center;gap:10px}
.hero-title{position:absolute;left:0;top:262px;width:1200px;text-align:center;font-family:"Lato",Arial,sans-serif;font-weight:900;font-size:68px;color:var(--white);text-shadow:0 3px 8px rgba(0,0,0,.45)}
.hero-sub{position:absolute;left:150px;top:344px;width:900px;text-align:center;font-size:18px;line-height:26px;font-weight:600;color:var(--white);text-shadow:0 2px 5px rgba(0,0,0,.5)}
.hero-actions{position:absolute;left:400px;top:416px;display:flex;gap:22px}
.hero-actions .btn{width:192px;height:58px;line-height:58px}

/* welcome */
.welcome-eyebrow{left:77px;top:778px}
.welcome-title{left:77px;top:806px;font-size:43px}
.welcome-text{left:437px;top:730px;width:690px;font-size:14px;line-height:27px}

/* services */
.services-eyebrow{left:77px;top:1106px}
.services-title{left:77px;top:1134px;font-size:43px}
.services-text{left:77px;top:1190px;width:440px;font-size:14px;line-height:27px}
.arrows{left:77px;top:1422px;display:flex;gap:14px}
.arrow-btn{width:46px;height:46px;background:var(--blue);border-radius:5px;display:flex;align-items:center;justify-content:center}

/* projects */
.project-tile{position:absolute;width:292px;height:197px}
.project-highlight{display:flex;flex-direction:column;align-items:center;justify-content:center;gap:22px;color:var(--white);font-family:"Lato",Arial,sans-serif;text-transform:uppercase}
.project-highlight .frame{position:absolute;inset:14px;border:1px solid rgba(255,255,255,.7)}
.projects-eyebrow{right:77px;top:1800px;text-align:right}
.projects-title{right:77px;top:1828px;font-size:43px}
.projects-btn{left:935px;top:1902px;width:188px;height:58px;line-height:58px}

/* interior */
.interior-eyebrow{left:77px;top:2432px}
.interior-title{left:77px;top:2460px;font-size:43px}
.interior-btn{left:77px;top:2538px;width:200px;height:58px;line-height:58px;font-size:18px}

/* news */
.news-eyebrow{left:0;top:2843px;width:1200px;text-align:center}
.news-title{left:0;top:2866px;width:1200px;text-align:center;font-size:43px}
.news-card{position:absolute;top:2950px;width:323px;height:398px;border:1px solid var(--line);background:var(--white)}
.news-photo{height:200px}
.news-date{position:absolute;left:14px;top:160px;width:80px;height:80px;border-radius:50%;background:var(--blue);border:4px solid var(--white);color:var(--white);font-family:"Lato",Arial,sans-serif;text-align:center;padding-top:10px}
.news-date b{display:block;font-size:28px;line-height:30px}
.news-date span{font-size:14px}
.news-author{position:absolute;left:100px;top:210px;font-family:"Lato",Arial,sans-serif;font-weight:700;font-size:14px;color:var(--blue-dark)}
.news-headline{position:absolute;left:14px;top:250px;width:295px;font-size:16px;line-height:24px;font-weight:600;color:var(--ink)}
.news-excerpt{position:absolute;left:14px;top:308px;width:295px;font-size:13px;line-height:24px;color:var(--muted)}

/* contact */
.contact{position:absolute;left:0;top:3408px;width:1200px;height:463px;background:linear-gradient(180deg,#3a79b4 0%,#1f5e9c 60%,#174f86 100%)}
.contact-eyebrow{left:0;top:66px;width:1200px;text-align:center;color:rgba(255,255,255,.75)}
.contact-title{left:0;top:90px;width:1200px;text-align:center;font-size:43px;color:var(--white)}
.field{position:absolute;background:rgba(255,255,255,.22);border:1px solid rgba(255,255,255,.45);border-radius:3px;color:var(--white);font-size:14px;padding:10px 12px}
.submit-btn{left:512px;top:358px;width:170px;height:50px;line-height:50px;font-size:18px;background:var(--blue-dark)}

/* footer */
.footer-col{position:absolute;top:3918px}
.footer-heading{font-family:"Lato",Arial,sans-serif;font-weight:900;font-size:16px;color:var(--blue-dark);text-transform:uppercase;margin-bottom:18px}
.footer-text{font-size:13px;line-height:24px;color:var(--ink)}
.footer-list{list-style:none;font-size:13px;line-height:29px;color:var(--ink)}
.footer-list li::before{content:"";display:inline-block;width:6px;height:6px;border-radius:50%;background:var(--blue-dark);margin-right:16px;vertical-align:middle}
.contact-row{display:flex;gap:16px;align-items:flex-start;font-size:13px;line-height:22px;margin-bottom:18px}
.social{display:flex;gap:12px}
.social span{width:36px;height:36px;border:1px solid var(--line);border-radius:3px;display:block}
.footer-bar{position:absolute;left:0;top:4200px;width:1200px;height:86px;background:var(--blue-dark)}
.footer-bump{position:absolute;left:557px;top:4160px;width:86px;height:86px;border-radius:50%;background:var(--blue-dark)}
.copyright{position:absolute;left:0;top:4250px;width:1200px;text-align:center;color:var(--white);font-size:14px}
</style>
</head>
<body>

<header class="hero">
  <div class="photo" role="img" aria-label="Photograph of a modern curved two-storey house with garden at dusk" style="inset:0;background:linear-gradient(180deg,#c5d0d8 0%,#9aa8b3 40%,#55644f 78%,#37433a 100%)"></div>
  <svg class="hero-overlay" width="1200" height="677" viewBox="0 0 1200 677" aria-hidden="true">
    <polygon points="0,0 600,0 0,677" fill="#1a6cb1" fill-opacity=".55"/>
    <polygon points="0,0 300,0 0,330" fill="#ffffff" fill-opacity=".35"/>
    <polygon points="0,677 0,500 300,677" fill="#0d4f8b"/>
    <polygon points="950,677 1200,420 1200,677" fill="#1a6cb1" fill-opacity=".6"/>
    <rect x="0" y="0" width="1200" height="677" fill="#000" fill-opacity=".12"/>
  </svg>
  <div class="brand"><div class="brand-square"></div><div class="brand-name">Kowhai<br>Homes</div></div>
  <div class="phone-box">
    <svg width="18" height="18" viewBox="0 0 24 24" aria-hidden="true"><path fill="#fff" d="M6.6 10.8a15 15 0 0 0 6.6 6.6l2.2-2.2c.3-.3.7-.4 1-.2 1.1.4 2.3.6 3.6.6.6 0 1 .4 1 1V20c0 .6-.4 1-1 1A17 17 0 0 1 3 4c0-.6.4-1 1-1h3.5c.6 0 1 .4 1 1 0 1.3.2 2.5.6 3.6.1.3 0 .7-.2 1z"/></svg>
    123 456 7890
  </div>
  <nav class="nav">
    <span class="nav-active">Home ▾</span><span>About</span><span>Services</span><span>Projects</span><span>News</span><span>Contact</span>
    <svg width="18" height="18" viewBox="0 0 24 24" aria-hidden="true"><circle cx="10" cy="10" r="7" fill="none" stroke="#fff" stroke-width="3"/><line x1="15" y1="15" x2="22" y2="22" stroke="#fff" stroke-width="3"/></svg>
  </nav>
  <h1 class="hero-title">WE BUILD YOUR DREAMS....</h1>
  <p class="hero-sub">Lorem Ipsum is simply dummy text of the printing and typesetting industry. Lorem Ipsum has been the industry's standard dummy text ever since the when an unknown.</p>
  <div class="hero-actions"><span class="btn">Learn More</span><span class="btn">Contact Us</span></div>
</header>

<section>
  <p class="abs eyebrow welcome-eyebrow">Welcome to</p>
  <h2 class="abs heading welcome-title">Kowhai Homes</h2>
  <div class="abs welcome-text">
    <p>Lorem Ipsum is simply dummy text of the printing and typesetting industry. Lorem Ipsum has been the industry's standard dummy text ever since the 1500s, when an unknown printer took a galley of type and scrambled it to make a type specimen book. It has survived not only five centuries, but also the leap into electronic typesetting, remaining essentially unchanged. It was popularised in the 1960s with the release of Tessaline sheets containing Lorem Ipsum passages, and more recently with desktop publishing software like Quillset Pagework including versions of Lorem Ipsum.</p>
    <a class="read-more">Read more.. »</a>
  </div>
</section>

<section>
  <p class="abs eyebrow services-eyebrow">Our Services</p>
  <h2 class="abs heading services-title">Residential House</h2>
  <div class="abs services-text">
    <p>Lorem Ipsum is simply dummy text of the printing and typesetting industry. Lorem Ipsum has been the industry's standard dummy text ever since the 1500s, when an unknown printer took a galley of type and scrambled it to make a type specimen book. It has survived not only five centuries, but also the leap into electronic typesetting, remaining essentially unchanged.</p>
    <a class="read-more" style="display:inline-block;margin-top:14px">Read more.. »</a>
  </div>
  <div class="abs arrows">
    <span class="arrow-btn"><svg width="18" height="14" viewBox="0 0 18 14" aria-hidden="true"><path d="M8 1 2 7l6 6M15 1 9 7l6 6" fill="none" stroke="#fff" stroke-width="2"/></svg></span>
    <span class="arrow-btn"><svg width="18" height="14" viewBox="0 0 18 14" aria-hidden="true"><path d="M3 1l6 6-6 6M10 1l6 6-6 6" fill="none" stroke="#fff" stroke-width="2"/></svg></span>
  </div>
  <div class="photo" role="img" aria-label="Photograph of a modern white residential house with glass balconies" style="left:571px;top:986px;width:629px;height:520px;clip-path:polygon(0 50%,22% 0,100% 0,100% 100%,22% 100%);background:linear-gradient(160deg,#d6dde3 0%,#a8b3bb 45%,#6f7b74 100%)"></div>
  <svg class="abs" style="left:571px;top:986px" width="629" height="520" viewBox="0 0 629 520" aria-hidden="true">
    <polygon points="460,0 629,0 629,520 560,520" fill="#1a6cb1" fill-opacity=".65"/>
    <polygon points="0,260 138,0 200,0" fill="#1a6cb1" fill-opacity=".5"/>
  </svg>
</section>

<section>
  <div class="photo project-tile" role="img" aria-label="Photograph of a two-storey suburban house" style="left:77px;top:1566px;background:linear-gradient(180deg,#c8d3dc,#7e7a70 60%,#5b6a48)"></div>
  <div class="project-tile project-highlight" style="left:389px;top:1566px;background:linear-gradient(180deg,#3f86c4,#1a6cb1)" role="img" aria-label="Featured project house photograph under a blue overlay">
    <span class="frame"></span>
    <span style="font-weight:900;font-size:20px">Project Title</span>
    <span style="font-size:13px;font-weight:700">View Detail</span>
  </div>
  <div class="photo project-tile" role="img" aria-label="Photograph of a modern white house with timber cladding" style="left:77px;top:1784px;background:linear-gradient(180deg,#9fbedb,#d7dadb 55%,#6c6f62)"></div>
  <div class="photo project-tile" role="img" aria-label="Photograph of timber house framing under construction" style="left:389px;top:1784px;background:linear-gradient(180deg,#a9c6e0,#c79b68 55%,#8b6a45)"></div>
  <div class="photo project-tile" role="img" aria-label="Photograph of a house frame with brick walls during construction" style="left:77px;top:1999px;background:linear-gradient(180deg,#c6d2dc,#a47a55 55%,#6f5a45)"></div>
  <div class="photo project-tile" role="img" aria-label="Photograph of a finished family home with front lawn" style="left:389px;top:1999px;background:linear-gradient(180deg,#b9cbe0,#c9c3b5 50%,#5d7a45)"></div>
  <p class="abs eyebrow projects-eyebrow">Wha we do</p>
  <h2 class="abs heading projects-title">Our Projects</h2>
  <span class="abs btn projects-btn">View All</span>
</section>

<section>
  <p class="abs eyebrow interior-eyebrow">House Designer</p>
  <h2 class="abs heading interior-title">Interior Design</h2>
  <span class="abs btn interior-btn">Contact Us</span>
  <div class="photo" role="img" aria-label="Photograph of a bright modern living room interior with television wall" style="left:571px;top:2257px;width:629px;height:520px;clip-path:polygon(0 50%,22% 0,100% 0,100% 100%,22% 100%);background:linear-gradient(135deg,#4a4f55 0%,#d9dcdf 45%,#bfc6cc 75%,#8e979e 100%)"></div>
  <svg class="abs" style="left:571px;top:2257px" width="629" height="520" viewBox="0 0 629 520" aria-hidden="true">
    <polygon points="0,260 138,0 260,0" fill="#1f2326" fill-opacity=".75"/>
    <polygon points="540,0 629,0 629,520 580,520" fill="#1a6cb1" fill-opacity=".8"/>
  </svg>
</section>

<section>
  <p class="abs eyebrow news-eyebrow">Recent updates</p>
  <h2 class="abs heading news-title">Latest News</h2>

  <article class="news-card" style="left:77px">
    <div class="photo news-photo" role="img" aria-label="Photograph of a family standing in a timber house frame" style="left:0;top:0;width:321px;background:linear-gradient(180deg,#d8c3a0,#b08656 60%,#7a5a3a)"></div>
    <div class="news-date"><b>06</b><span>Nov</span></div>
    <p class="news-author">by Kowhai Homes</p>
    <h3 class="news-headline">Lorem Ipsum is the simply dummy text of the printing and ?</h3>
    <p class="news-excerpt">Lorem Ipsum is the simply dummy text of the printing and typesetting industry Lorem Ipsum has been the industry's...</p>
  </article>
  <article class="news-card" style="left:440px">
    <div class="photo news-photo" role="img" aria-label="Photograph of a two-storey stone and timber house" style="left:0;top:0;width:321px;background:linear-gradient(180deg,#9fbfe0,#c2b5a3 55%,#5f7448)"></div>
    <div class="news-date"><b>06</b><span>Nov</span></div>
    <p class="news-author">by Kowhai Homes</p>
    <h3 class="news-headline">Lorem Ipsum is the simply dummy text of the printing and ?</h3>
    <p class="news-excerpt">Lorem Ipsum is the simply dummy text of the printing and typesetting industry Lorem Ipsum has been the industry's...</p>
  </article>
  <article class="news-card" style="left:800px">
    <div class="photo news-photo" role="img" aria-label="Photograph of builders reviewing plans inside a framed house" style="left:0;top:0;width:321px;background:linear-gradient(180deg,#e2cfae,#b88a5a 55%,#7c5837)"></div>
    <div class="news-date"><b>06</b><span>Nov</span></div>
    <p class="news-author">by Kowhai Homes</p>
    <h3 class="news-headline">Lorem Ipsum is the simply dummy text of the printing and ?</h3>
    <p class="news-excerpt">Lorem Ipsum is the simply dummy text of the printing and typesetting industry Lorem Ipsum has been the industry's...</p>
  </article>
</section>

<section class="contact" role="img" aria-label="Contact form over a blue-tinted photograph of a house">
  <p class="abs eyebrow contact-eyebrow">Contact us</p>
  <h2 class="abs heading contact-title">Get in Touch</h2>
  <div class="field" style="left:232px;top:170px;width:330px;height:44px">Name*</div>
  <div class="field" style="left:232px;top:224px;width:330px;height:44px">Email*</div>
  <div class="field" style="left:232px;top:278px;width:330px;height:44px">Phone*</div>
  <div class="field" style="left:572px;top:170px;width:396px;height:152px">Message*</div>
  <span class="abs btn submit-btn">Submit</span>
</section>

<footer>
  <div class="footer-col" style="left:77px;width:230px">
    <h4 class="footer-heading">About us</h4>
    <p class="footer-text">Lorem Ipsum is the simply dummy text of the printing and typesetting industry Lorem Ipsum has been the industry's...</p>
    <p class="footer-text" style="margin-top:12px">Lorem Ipsum is the simply dummy text of the printing and...</p>
    <a class="read-more" style="display:inline-block;margin-top:8px">Read more.. »</a>
  </div>
  <div class="footer-col" style="left:342px">
    <h4 class="footer-heading">Site map</h4>
    <ul class="footer-list"><li>Home</li><li>About</li><li>Services</li><li>Projects</li><li>News</li><li>Contact</li></ul>
  </div>
  <div class="footer-col" style="left:608px">
    <h4 class="footer-heading">Services</h4>
    <ul class="footer-list"><li>Residential House</li><li>light commercial</li><li>Interior Design</li></ul>
  </div>
  <div class="footer-col" style="left:873px;width:260px">
    <h4 class="footer-heading">Site map</h4>
    <div class="contact-row">
      <svg width="18" height="24" viewBox="0 0 18 24" aria-hidden="true"><path d="M9 0a9 9 0 0 0-9 9c0 7 9 15 9 15s9-8 9-15a9 9 0 0 0-9-9zm0 13a4 4 0 1 1 0-8 4 4 0 0 1 0 8z" fill="#0d4f8b"/></svg>
      <div><b style="color:var(--blue-dark);font-family:Lato,sans-serif">KOWHAI HOMES</b><br>101 - Lorem Ipsum Is Simple Dummy Text of Print</div>
    </div>
    <div class="contact-row">
      <svg width="18" height="18" viewBox="0 0 24 24" aria-hidden="true"><path fill="#0d4f8b" d="M6.6 10.8a15 15 0 0 0 6.6 6.6l2.2-2.2c.3-.3.7-.4 1-.2 1.1.4 2.3.6 3.6.6.6 0 1 .4 1 1V20c0 .6-.4 1-1 1A17 17 0 0 1 3 4c0-.6.4-1 1-1h3.5c.6 0 1 .4 1 1 0 1.3.2 2.5.6 3.6.1.3 0 .7-.2 1z"/></svg>
      <span>123 456 7890</span>
    </div>
    <div class="contact-row">
      <svg width="18" height="14" viewBox="0 0 18 14" aria-hidden="true"><rect width="18" height="14" rx="1" fill="#0d4f8b"/><path d="M1 1l8 6 8-6" fill="none" stroke="#fff" stroke-width="1.5"/></svg>
      <span>info@kowhaihomes.com</span>
    </div>
    <div class="social" aria-label="Social links"><span></span><span></span><span></span></div>
  </div>
  <div class="footer-bar"></div>
  <div class="footer-bump"></div>
  <p class="copyright">©KOWHAI HOMES · 2017 · All Rights Reserved.</p>
</footer>

</body>
</html>
```